New letter head for Air Conditioning business

We need a new professional letter head design to suit our new re-branded air conditioning business. Our new logo is attached

```html
<!DOCTYPE html>
<html lang="en">
<head>
<meta charset="utf-8">
<title>Corvane Letterhead</title>
<link href="https://fonts.googleapis.com/css2?family=Open+Sans:wght@400;600&family=Lato:wght@400&display=swap" rel="stylesheet">
<style>
  :root {
    --green: #64c18a;
    --charcoal: #333436;
    --coral: #ef6b5d;
    --ink: #4a4a4a;
    --ink-dark: #2e2e2e;
    --paper: #ffffff;
    --backdrop: #e6e6e6;
  }
  * { margin: 0; padding: 0; box-sizing: border-box; }
  html, body { width: 1040px; height: 1200px; overflow: hidden; background: var(--backdrop); }
  .letterhead {
    position: absolute; left: 53px; top: 0;
    width: 934px; height: 1200px;
    background: var(--paper);
    font-family: "Open Sans", sans-serif;
    color: var(--ink);
  }
  .top-band { position: absolute; left: 0; top: 0; width: 100%; height: 16px; background: var(--green); }
  .brand { position: absolute; left: 89px; top: 40px; display: flex; align-items: center; gap: 18px; }
  .brand-mark { width: 52px; height: 52px; background: var(--green); }
  .brand-name { font-size: 44px; font-weight: 600; letter-spacing: 6px; color: var(--charcoal); line-height: 1; }
  .letter-body { position: absolute; left: 89px; top: 216px; width: 754px; font-size: 14.5px; }
  .issue-date { margin-bottom: 17px; }
  .recipient { line-height: 18px; margin-bottom: 49px; }
  .salutation { margin-bottom: 33px; }
  .letter-body p.paragraph { text-align: justify; line-height: 27px; margin-bottom: 27px; }
  .closing { margin-top: 57px; }
  .signature {
    width: 215px; height: 28px; margin-top: 14px;
    background: linear-gradient(90deg, #d9d9d9, #efefef);
  }
  .signer-name { font-size: 19px; font-weight: 600; color: var(--ink-dark); margin-top: 12px; }
  .signer-title { font-size: 14.5px; margin-top: 5px; }
  .contacts { position: absolute; right: 92px; top: 1016px; font-family: "Lato", sans-serif; font-size: 17.5px; color: #1f1f1f; }
  .contact-row { display: flex; align-items: center; justify-content: flex-end; gap: 12px; height: 36px; margin-bottom: 15px; }
  .contact-text { text-align: right; line-height: 21px; }
  .contact-icon { width: 36px; height: 36px; display: flex; align-items: center; justify-content: center; flex: none; }
  .icon-phone { background: var(--green); }
  .icon-web { background: var(--charcoal); }
  .icon-pin { background: var(--coral); }
  .footer-bands { position: absolute; left: 0; bottom: 0; }
</style>
</head>
<body>
<main class="letterhead">
  <div class="top-band"></div>

  <header class="brand">
    <div class="brand-mark"></div>
    <div class="brand-name">CORVANE</div>
  </header>

  <section class="letter-body">
    <div class="issue-date">Issuing Date: May 5, 2018</div>
    <div class="recipient">Name Of Employee Mr. XYZABC<br>Address of Employee<br>Address Line 2 etc..</div>
    <div class="salutation">Dear Mr.XYZABC</div>
    <p class="paragraph">Lorem Ipsum has been the industry's standard dummy text ever since the 1500s, when an unknown printer took a galley of type and scrambled it to make a type specimen book. It has survived not only five centuries, but also the leap into electronic typesetting, remaining essentially unchanged. It was popularised in the 1960s with the release of Letraset sheets containing Lorem Ipsum passages, and more recently with desktop publishing software like Aldus PageMaker including versions of Lorem Ipsum.</p>
    <p class="paragraph">Lorem Ipsum is simply dummy text of the printing and typesetting industry. Lorem Ipsum has been the industry's standard dummy text ever since the 1500s, when an unknown printer took a galley of type and scrambled it to make a type specimen book.</p>
    <p class="paragraph">It has survived not only five centuries, but also the leap into electronic typesetting, remaining essentially unchanged. It was popularised in the 1960s with the release of Letraset sheets containing Lorem IpsumIpsum passages.</p>
    <div class="closing">Yours Sincerely</div>
    <div class="signature" role="img" aria-label="Handwritten signature of Daniel Hartley"></div>
    <div class="signer-name">Daniel Hartley</div>
    <div class="signer-title">Managing Director</div>
  </section>

  <section class="contacts">
    <div class="contact-row">
      <div class="contact-text">044-555 010 234<br>044-555 010 234</div>
      <div class="contact-icon icon-phone">
        <svg width="18" height="18" viewBox="0 0 24 24"><path fill="#fff" d="M6.6 10.8c1.4 2.8 3.8 5.1 6.6 6.6l2.2-2.2c.3-.3.7-.4 1-.2 1.1.4 2.3.6 3.6.6.6 0 1 .4 1 1V20c0 .6-.4 1-1 1C10.6 21 3 13.4 3 4c0-.6.4-1 1-1h3.5c.6 0 1 .4 1 1 0 1.3.2 2.5.6 3.6.1.3 0 .7-.2 1z"/></svg>
      </div>
    </div>
    <div class="contact-row">
      <div class="contact-text">info@corvane-air.com<br>www.corvane-air.com</div>
      <div class="contact-icon icon-web">
        <svg width="20" height="20" viewBox="0 0 24 24"><circle cx="12" cy="12" r="9" fill="#fff"/><path fill="#333436" d="M8 7l3 1 1 3-2 2 1 4-3-3-1-4zM14 13l3 1-1 4-3 1z"/></svg>
      </div>
    </div>
    <div class="contact-row">
      <div class="contact-text">87, Maple Street West<br>Northfield, 30918</div>
      <div class="contact-icon icon-pin">
        <svg width="16" height="20" viewBox="0 0 16 22"><path fill="#fff" d="M8 0C3.6 0 0 3.6 0 8c0 6 8 14 8 14s8-8 8-14c0-4.4-3.6-8-8-8zm0 11a3 3 0 1 1 0-6 3 3 0 0 1 0 6z"/></svg>
      </div>
    </div>
  </section>

  <svg class="footer-bands" width="934" height="59" viewBox="0 0 934 59">
    <polygon points="0,0 225,0 244,59 0,59" fill="var(--green)"/>
    <polygon points="235,32 569,32 583,59 244,59" fill="var(--charcoal)"/>
    <polygon points="569,32 934,32 934,59 583,59" fill="var(--coral)"/>
  </svg>
</main>
</body>
</html>
```